Coastal Learner Bureau business cards

Australian company about to start offering its services. We recruit international students to come to study English, vocational education and postgraduate courses in Australia. We help them find the institution and select the right city they want to come to Australia. We are a young, online oriented and supportive agency. Our clients are between 18 and 35 years old, mainly University students, young professionals or people with work experience. We provide much more information that any other agency offer. We administrate a Facebook group with more than 11.000 members that daily ask questions about general information when coming to Australia, while they are here and even after they leave the country

Target Market(s)

International students from South America, Central America and Europe

Industry/Entity Type

Student

Contact Information for Business Card

Tomas Bilbrea
Managing Director
tomas@kelvarin.com.au
www.kelvoria.com.au
+61 491058264
Melbourne, Australia

Font styles to use
Serif
Sans Serif

Colors

Designer to choose colors to be used in the design.

Requirements
Must have
• Horizontal design
• Standard business card size and shape. If font uses green or yellow colours, they will have to match the ones from the logo
Nice to have
• UPDATE: Use the contents of the green image to design one of the card sides. Use our logo in the background of that side as watermark.
• Passport image, or immigration stamps. A picture of the Yarra River (from Melbourne) would be cool as well.
Should not have
• Non-standard business card size and shape
• Not black as the background colour of any sides as we are not a VIP agency or a hight class service. We are orientes to young people and they like colours, pictures, something attractive.
• Vertical design
• NO YELLOW or BLACK AS THE BACKGROUND COLOUR OF ANY SIDE OF THE BIZ CARD

```html
<!DOCTYPE html>
<html lang="en">
<head>
<meta charset="utf-8">
<title>Coastal Learner Bureau business cards</title>
<link rel="stylesheet" href="https://fonts.googleapis.com/css2?family=Jost:wght@400;500&family=Oswald:wght@600&display=swap">
<style>
  :root {
    --backdrop: #8e8c8d;
    --card-front: #1b5e3b;
    --card-light: #ffffff;
    --brand-green: #1b5e3b;
    --brand-yellow: #e3b520;
    --text-grey: #4a4a4a;
    --text-white: #ffffff;
  }
  * { margin: 0; padding: 0; box-sizing: border-box; }
  html, body {
    width: 1200px;
    height: 929px;
    overflow: hidden;
    background: var(--backdrop);
    font-family: "Jost", sans-serif;
  }
  .canvas {
    position: relative;
    width: 1200px;
    height: 929px;
  }
  .card {
    position: absolute;
    width: 560px;
    height: 320px;
    box-shadow: 0 10px 24px rgba(0,0,0,0.28);
  }
  .card--front {
    left: 110px;
    top: 90px;
    background: var(--card-front);
  }
  .card--back {
    left: 530px;
    top: 510px;
    background: var(--card-light);
  }
  .brand {
    position: absolute;
    left: 0;
    right: 0;
    top: 110px;
    display: flex;
    justify-content: center;
    align-items: center;
    gap: 12px;
  }
  .brand__dot {
    width: 18px;
    height: 18px;
    border-radius: 50%;
    background: var(--brand-yellow);
  }
  .brand__name {
    font-family: "Jost", sans-serif;
    font-weight: 500;
    font-size: 52px;
    line-height: 1.2;
    color: var(--text-white);
    letter-spacing: 1px;
  }
  .tagline {
    position: absolute;
    left: 0;
    right: 0;
    top: 238px;
    text-align: center;
    font-size: 14px;
    letter-spacing: 1.2px;
    color: var(--text-white);
  }
  .identity {
    position: absolute;
    right: 318px;
    top: 128px;
    text-align: right;
    white-space: nowrap;
  }
  .identity__name {
    font-family: "Oswald", sans-serif;
    font-weight: 600;
    font-size: 27px;
    line-height: 1;
    color: var(--brand-green);
    text-transform: uppercase;
    letter-spacing: 0.3px;
  }
  .identity__role {
    margin-top: 6px;
    font-size: 17px;
    color: var(--text-grey);
    letter-spacing: 0.6px;
  }
  .divider {
    position: absolute;
    left: 258px;
    top: 104px;
    width: 2px;
    height: 104px;
    background: var(--brand-green);
  }
  .contact {
    position: absolute;
    left: 278px;
    top: 104px;
    list-style: none;
    white-space: nowrap;
  }
  .contact__item {
    display: flex;
    align-items: center;
    gap: 10px;
    height: 26px;
    font-size: 15px;
    color: var(--text-grey);
    letter-spacing: 0.6px;
  }
  .contact__icon {
    width: 13px;
    height: 13px;
    flex: none;
  }
</style>
</head>
<body>
<main class="canvas">
  <section class="card card--front" aria-label="Card front">
    <div class="brand">
      <span class="brand__dot"></span>
      <span class="brand__name">Kelvoria</span>
    </div>
    <p class="tagline">Hacemos más por ti!</p>
  </section>

  <section class="card card--back" aria-label="Card back">
    <div class="identity">
      <h1 class="identity__name">Tomas Bilbrea</h1>
      <p class="identity__role">Managing Director</p>
    </div>
    <div class="divider"></div>
    <ul class="contact">
      <li class="contact__item">
        <svg class="contact__icon" viewBox="0 0 13 13"><rect x="3" y="0.8" width="7" height="11.4" rx="1.2" fill="none" stroke="var(--brand-green)" stroke-width="1.4"/></svg>
        +61 491058264
      </li>
      <li class="contact__item">
        <svg class="contact__icon" viewBox="0 0 13 13"><rect x="0.5" y="2.5" width="12" height="8" fill="var(--brand-green)"/><path d="M0.5 2.5 L6.5 7 L12.5 2.5" fill="none" stroke="#fff" stroke-width="1"/></svg>
        tomas@kelvarin.com.au
      </li>
      <li class="contact__item">
        <svg class="contact__icon" viewBox="0 0 13 13"><circle cx="5.2" cy="5.2" r="3.8" fill="none" stroke="var(--brand-green)" stroke-width="1.6"/><line x1="8" y1="8" x2="12" y2="12" stroke="var(--brand-green)" stroke-width="1.8"/></svg>
        www.kelvoria.com.au
      </li>
      <li class="contact__item">
        <svg class="contact__icon" viewBox="0 0 13 13"><path d="M6.5 12.5 C3 8 2 6.5 2 4.8 A4.5 4.5 0 0 1 11 4.8 C11 6.5 10 8 6.5 12.5 Z" fill="var(--brand-green)"/><circle cx="6.5" cy="4.8" r="1.6" fill="#fff"/></svg>
        Melbourne, Australia
      </li>
    </ul>
  </section>
</main>
</body>
</html>
```